birchwell hollow cattle company website

we would like a home page, an about us page, a page for sires, a page for dams, A sale page where we can list progreny for sale and a contact us. on the about us page we would like there to be a family picture. on the sires page we would like to have a picture of each sire, a description beside them and a link to their online profile at northern hereford registry. on the dam page we would like to have a picture of each dam, aswell as a description beside them aswell as a link to the northern hereford registry site. would like the website to very mobile phone friendly as expecting most traffic to be on phone. we would like the website to look and feel very mich like a farm, rustic, barbed wire and other farm feels. we would also like a frozen genetics pages where we can include pictures and descriptions of the sires and dams aswell as a price for embryos and semen. we need to website to be easy to maintain so we can update pictures and information as it changes, we would like there to be a feature so that people can sign up to be on our mailing list by giving us their mailing addess and email and full name
aswell as an area where they can send us a message to contact us.

leaving for work for 3 weeks in the canadian arctic will have limited ability to use the internet

Target Market(s)

other ranchers, farmers, cattlemen,

Industry/Entity Type

farming, agriculture, cattle

Coding

Coded - Design and coding required

Requirements
Must have
• about page, contact page, sires page, dams page, SALE page.
Nice to have
• country/farm vibe, barbed wire, wood,

```html
<!DOCTYPE html>
<html lang="en">
<head>
<meta charset="utf-8">
<title>Birchwell Hollow Cattle Company</title>
<link href="https://fonts.googleapis.com/css2?family=Oswald:wght@400;500&family=Poppins:wght@400;500;600&display=swap" rel="stylesheet">
<style>
:root{
  --wood:#2a2320;
  --wood-deep:#221c19;
  --peach:#f8d6b2;
  --peach-light:#fbe4cb;
  --ink:#2b2522;
  --body:#3d3530;
  --muted:#7a706a;
  --white:#ffffff;
  --wire:#8b8581;
  --btn-dark:#2a2624;
}
*{box-sizing:border-box;margin:0;padding:0}
html,body{width:1200px;height:4367px;overflow:hidden}
body{font-family:"Poppins",sans-serif;color:var(--body);background:var(--wood);position:relative}
.heading{font-family:"Oswald",sans-serif;font-weight:500;text-transform:uppercase;letter-spacing:.5px;text-align:center}
section,header,footer{position:absolute;left:0;width:1200px}
.btn{display:inline-block;font-family:"Oswald",sans-serif;font-weight:500;text-transform:uppercase;text-decoration:none;border-radius:30px;text-align:center}
.btn-light{background:var(--white);color:var(--ink)}
.btn-dark{background:var(--btn-dark);color:var(--white)}
.wire{position:absolute;left:0;width:1200px;height:20px}

/* nav */
.site-nav{top:0;height:76px;background:linear-gradient(#2c2420,#3a2c24);z-index:3}
.site-nav ul{list-style:none;display:flex;position:absolute;top:28px;left:158px;gap:0}
.site-nav li{font-size:15px;color:#e9e2dc;letter-spacing:.3px;margin-right:65px}
.site-nav li.active{font-weight:600;color:#fff}

/* hero */
.hero{top:76px;height:690px;overflow:hidden}
.hero-photo{position:absolute;inset:0;background:linear-gradient(180deg,#2d3440 0%,#3b4450 30%,#262a25 55%,#1e2618 78%,#2c3a1e 100%)}
.hero-brand{position:absolute;top:190px;width:100%;text-align:center;font-family:"Oswald",sans-serif;font-weight:500;color:#fff;font-size:38px;line-height:44px;text-transform:uppercase}
.hero-title{position:absolute;top:345px;width:100%;color:#fff;font-size:62px;line-height:70px}
.hero .btn{position:absolute;top:502px;left:537px;width:126px;height:50px;line-height:50px;font-size:15px}
.hero-curve{position:absolute;bottom:0;left:0}

/* featured sires */
.sires{top:755px;height:790px;background:linear-gradient(180deg,var(--peach-light),var(--peach) 50%,var(--peach-light))}
.section-icon{position:absolute;left:560px;width:80px;height:40px;border-radius:6px}
.sires .section-icon{top:60px;background:#2d2723}
.sires .heading{position:absolute;top:108px;width:100%;font-size:54px;color:var(--ink)}
.sires .lead{position:absolute;top:190px;left:160px;width:880px;text-align:center;font-size:15px;line-height:29px;color:var(--ink)}
.sire-card{position:absolute;top:282px;width:293px;height:387px;background:#fff;border-radius:14px;text-align:center}
.sire-photo{position:absolute;top:0;left:12px;width:269px;height:227px;border-radius:12px}
.sire-card h3{position:absolute;top:240px;width:100%;font-size:17px;font-weight:500;color:var(--ink)}
.sire-card p{position:absolute;top:278px;left:28px;width:237px;font-size:13px;line-height:25px;color:var(--muted)}
.sire-card a{position:absolute;top:355px;width:100%;left:0;font-size:15px;color:var(--ink);text-decoration:underline}
.slider-arrow{position:absolute;top:460px;width:32px;height:32px}

/* about */
.about{top:1545px;height:812px;background:linear-gradient(180deg,var(--wood),var(--wood-deep) 50%,var(--wood))}
.about .section-icon{top:110px;background:#f2ede8}
.about .heading{position:absolute;top:158px;width:100%;font-size:56px;color:#fff}
.family-photo{position:absolute;top:274px;left:112px;width:422px;height:385px;border-radius:20px;border:2px solid #fff;background:linear-gradient(160deg,#6b4a34,#4a3a30 50%,#8a8278)}
.seal{position:absolute;top:555px;left:423px;width:154px;height:154px;border-radius:50%;background:#1b1816;border:5px solid #d8b45a}
.about-text{position:absolute;top:268px;left:617px;width:471px;font-size:14.5px;line-height:25.7px;color:#f1ebe5;text-align:justify}
.about-text p+p{margin-top:25px}
.about .btn{position:absolute;top:667px;left:617px;width:126px;height:50px;line-height:50px;font-size:15px}

/* frozen genetics */
.frozen{top:2357px;height:950px;background:linear-gradient(180deg,var(--peach-light),var(--peach) 60%,var(--peach-light))}
.frozen .section-icon{top:110px;background:#2d2723}
.frozen .heading{position:absolute;top:160px;width:100%;font-size:56px;line-height:60px;color:var(--ink)}
.frozen h3{position:absolute;top:298px;width:100%;text-align:center;font-size:20px;font-weight:600;color:var(--ink)}
.frozen .copy{position:absolute;top:328px;left:160px;width:880px;text-align:center;font-size:15px;line-height:29px;color:var(--ink)}
.frozen .copy p+p{margin-top:28px}
.frozen .btn{position:absolute;top:553px;left:495px;width:210px;height:52px;line-height:52px;font-size:15px}
.herd-photo{position:absolute;top:660px;left:0;width:1200px;height:290px;background:linear-gradient(180deg,#f3cfa8 0%,#a0562e 30%,#7a3a20 60%,#4f6a2a 85%,#3f5a22 100%)}

/* newsletter */
.newsletter{top:3307px;height:576px;background:linear-gradient(180deg,var(--wood),var(--wood-deep))}
.newsletter .section-icon{top:112px;background:#f2ede8}
.newsletter .heading{position:absolute;top:166px;width:100%;font-size:58px;color:#fff}
.newsletter .lead{position:absolute;top:256px;left:280px;width:640px;text-align:center;font-size:19px;line-height:33px;color:#f1ebe5}
.email-field{position:absolute;top:337px;left:202px;width:796px;height:65px;border:1.5px solid #9a928c;border-radius:34px;background:rgba(255,255,255,.06);font-size:15px;color:#f1ebe5;padding:0 0 0 33px;line-height:62px}
.newsletter .btn{position:absolute;top:434px;left:500px;width:198px;height:62px;line-height:62px;font-size:20px}

/* footer */
.site-footer{top:3883px;height:484px;background:var(--wood)}
.footer-brand{position:absolute;top:168px;left:110px;width:290px;text-align:center;font-family:"Oswald",sans-serif;font-weight:500;font-size:34px;line-height:40px;color:#fff;text-transform:uppercase}
.footer-col{position:absolute;top:128px}
.footer-col h4{font-family:"Oswald",sans-serif;font-weight:400;font-size:20px;color:#fff;text-transform:uppercase;margin-bottom:12px}
.footer-col ul{list-style:none}
.footer-col li{font-size:15px;color:#f1ebe5;height:34px;display:flex;align-items:center;gap:10px}
.footer-col li svg{flex:none}
.contact-list li{height:auto;align-items:flex-start;margin-bottom:16px;line-height:27px}
.contact-list .ico{width:30px;height:30px;border-radius:50%;background:#fff;display:flex;align-items:center;justify-content:center;flex:none}
.footer-rule{position:absolute;top:375px;left:112px;width:976px;height:1px;background:#4e4540}
.copyright{position:absolute;top:408px;width:100%;text-align:center;font-size:15px;font-weight:500;color:#fff}
</style>
</head>
<body>

<header class="site-nav">
  <nav>
    <ul>
      <li class="active">HOME</li>
      <li>ABOUT US</li>
      <li>SIRES</li>
      <li>DAMS</li>
      <li>FROZEN GENETICS</li>
      <li>SALE</li>
      <li>CONTACT US</li>
    </ul>
  </nav>
</header>

<section class="hero">
  <div class="hero-photo" role="img" aria-label="Herd of black cattle in a pasture under a stormy evening sky"></div>
  <div class="hero-brand">Birchwell Hollow<br>Cattle Company</div>
  <h1 class="heading hero-title">Welcome to Birchwell Hollow<br>Cattle Company</h1>
  <a class="btn btn-light" href="#">Get Started</a>
  <svg class="hero-curve" width="1200" height="60" viewBox="0 0 1200 60" aria-hidden="true">
    <path d="M0 60 L0 44 Q600 -30 1200 44 L1200 60 Z" fill="#1e1a18"/>
    <path d="M0 60 L0 52 Q600 -8 1200 52 L1200 60 Z" fill="#fbe4cb"/>
  </svg>
</section>

<section class="sires">
  <div class="section-icon" role="img" aria-label="Small cattle silhouette icon"></div>
  <h2 class="heading">Featured Sires</h2>
  <p class="lead">Our sires represent the heart of the Birchwell Hollow breeding program—selected for structural soundness, fertility, muscle expression, maternal strength, and real-world performance.</p>

  <svg class="slider-arrow" style="left:38px" viewBox="0 0 32 32" aria-label="Previous"><circle cx="16" cy="16" r="14" fill="none" stroke="#2b2522" stroke-width="2"/><path d="M22 16H10M15 11l-5 5 5 5" fill="none" stroke="#2b2522" stroke-width="2"/></svg>
  <svg class="slider-arrow" style="left:1126px" viewBox="0 0 32 32" aria-label="Next"><circle cx="16" cy="16" r="14" fill="none" stroke="#2b2522" stroke-width="2"/><path d="M10 16h12M17 11l5 5-5 5" fill="none" stroke="#2b2522" stroke-width="2"/></svg>

  <article class="sire-card" style="left:112px">
    <div class="sire-photo" role="img" aria-label="Red Angus bull standing in dry grass" style="background:linear-gradient(180deg,#b7b48c,#8a3a1e 50%,#9c9a64)"></div>
    <h3>BH Northwind 21K</h3>
    <p>Ideal for commercial or registered programs aiming for predictable performance.</p>
    <a href="#">Read More</a>
  </article>
  <article class="sire-card" style="left:453px">
    <div class="sire-photo" role="img" aria-label="Group of black Angus cattle in green pasture" style="background:linear-gradient(180deg,#9aa7a0,#1f2220 45%,#4e8a2e)"></div>
    <h3>BH Cedar Ridge 37M</h3>
    <p>Ideal for commercial or registered programs aiming for predictable performance.</p>
    <a href="#">Read More</a>
  </article>
  <article class="sire-card" style="left:793px">
    <div class="sire-photo" role="img" aria-label="Black Angus cow on a green hillside" style="background:linear-gradient(180deg,#8fb8d8,#5d8a3e 40%,#1e2220 65%,#6a9a3a)"></div>
    <h3>BH Stonefield 805J</h3>
    <p>Ideal for commercial or registered programs aiming for predictable performance.</p>
    <a href="#">Read More</a>
  </article>

  <svg class="wire" style="top:778px" viewBox="0 0 1200 20" aria-hidden="true"><line x1="0" y1="9" x2="1200" y2="9" stroke="#8b8581" stroke-width="2"/><line x1="0" y1="12" x2="1200" y2="12" stroke="#5e5854" stroke-width="2"/></svg>
</section>

<section class="about">
  <div class="section-icon" role="img" aria-label="Small cattle silhouette icon"></div>
  <h2 class="heading">About Birchwell Hollow Cattle</h2>
  <div class="family-photo" role="img" aria-label="Ranch family of four standing in front of a wooden barn with their dog"></div>
  <div class="seal" role="img" aria-label="Premium quality seal"></div>
  <div class="about-text">
    <p>Birchwell Hollow Cattle Company is a family-run Angus operation grounded in tradition, integrity, and a deep respect for the land we call home. What started as a small group of cattle has grown into a focused breeding program built on quality, consistency, and real-world performance.</p>
    <p>For us, ranching isn’t just a business—it’s a way of life. Every season, every calf, and every decision we make is guided by our commitment to raising cattle that not only look good in the pasture, but work hard for the families and ranches who rely on them. We breed with purpose—and we stand behind the cattle we raise. We take pride in passing down the values of hard work, honesty, and stewardship to the next generation. Ranching is something we do together. For us, ranching isn’t just a business—it’s a way of life.</p>
  </div>
  <a class="btn btn-light" href="#">Read More</a>
  <svg class="wire" style="top:800px" viewBox="0 0 1200 20" aria-hidden="true"><line x1="0" y1="9" x2="1200" y2="9" stroke="#8b8581" stroke-width="2"/><line x1="0" y1="12" x2="1200" y2="12" stroke="#5e5854" stroke-width="2"/></svg>
</section>

<section class="frozen">
  <div class="section-icon" role="img" aria-label="Small cattle silhouette icon"></div>
  <h2 class="heading">Embryos &amp; Semen: Birchwell<br>Hollow Frozen Genetics</h2>
  <h3>Premium Genetics for Progressive Breeders</h3>
  <div class="copy">
    <p>At Birchwell Hollow Cattle Company, we are proud to offer a carefully curated selection of frozen genetics from the sires and dams that anchor our program. These embryos and semen lots represent the very best of our herd—cattle selected for structural correctness, fertility, performance, and long-term functionality.</p>
    <p>Our frozen genetics allow breeders to access the same proven lines that have shaped our cow family for generations. Whether you’re looking to strengthen maternal traits, add dimension and muscle, or introduce balanced, reliable Angus genetics into your program, our offerings provide a trusted foundation.</p>
  </div>
  <a class="btn btn-dark" href="#">Order Frozen Genetics</a>
  <div class="herd-photo" role="img" aria-label="Line of red and black cattle standing in green grass at sunset"></div>
</section>

<section class="newsletter">
  <svg class="wire" style="top:-10px" viewBox="0 0 1200 20" aria-hidden="true"><line x1="0" y1="9" x2="1200" y2="9" stroke="#8b8581" stroke-width="2"/><line x1="0" y1="12" x2="1200" y2="12" stroke="#5e5854" stroke-width="2"/></svg>
  <div class="section-icon" role="img" aria-label="Small cattle silhouette icon"></div>
  <h2 class="heading">Join Our Newsletter</h2>
  <p class="lead">Join our mailing list to receive exclusive updates straight from the ranch. Be the first to hear about:</p>
  <div class="email-field">Enter The Email</div>
  <a class="btn btn-light" href="#">Subscribe Us</a>
  <svg class="wire" style="top:566px" viewBox="0 0 1200 20" aria-hidden="true"><line x1="0" y1="9" x2="1200" y2="9" stroke="#8b8581" stroke-width="2"/><line x1="0" y1="12" x2="1200" y2="12" stroke="#5e5854" stroke-width="2"/></svg>
</section>

<footer class="site-footer">
  <div class="footer-brand">Birchwell Hollow<br>Cattle Company</div>

  <div class="footer-col" style="left:447px">
    <h4>Quick Links</h4>
    <ul>
      <li><svg width="12" height="12" viewBox="0 0 12 12"><path d="M1 6h9M6 2l4 4-4 4" fill="none" stroke="#fff" stroke-width="2"/></svg>Home</li>
      <li><svg width="12" height="12" viewBox="0 0 12 12"><path d="M1 6h9M6 2l4 4-4 4" fill="none" stroke="#fff" stroke-width="2"/></svg>About</li>
      <li><svg width="12" height="12" viewBox="0 0 12 12"><path d="M1 6h9M6 2l4 4-4 4" fill="none" stroke="#fff" stroke-width="2"/></svg>Sires</li>
      <li><svg width="12" height="12" viewBox="0 0 12 12"><path d="M1 6h9M6 2l4 4-4 4" fill="none" stroke="#fff" stroke-width="2"/></svg>Dams</li>
      <li><svg width="12" height="12" viewBox="0 0 12 12"><path d="M1 6h9M6 2l4 4-4 4" fill="none" stroke="#fff" stroke-width="2"/></svg>Contact Us</li>
    </ul>
  </div>

  <div class="footer-col" style="left:646px">
    <h4>Help Links</h4>
    <ul>
      <li><svg width="12" height="12" viewBox="0 0 12 12"><path d="M1 6h9M6 2l4 4-4 4" fill="none" stroke="#fff" stroke-width="2"/></svg>FAQ</li>
      <li><svg width="12" height="12" viewBox="0 0 12 12"><path d="M1 6h9M6 2l4 4-4 4" fill="none" stroke="#fff" stroke-width="2"/></svg>Terms of use</li>
      <li><svg width="12" height="12" viewBox="0 0 12 12"><path d="M1 6h9M6 2l4 4-4 4" fill="none" stroke="#fff" stroke-width="2"/></svg>Privacy Policy</li>
      <li><svg width="12" height="12" viewBox="0 0 12 12"><path d="M1 6h9M6 2l4 4-4 4" fill="none" stroke="#fff" stroke-width="2"/></svg>Support Links</li>
      <li><svg width="12" height="12" viewBox="0 0 12 12"><path d="M1 6h9M6 2l4 4-4 4" fill="none" stroke="#fff" stroke-width="2"/></svg>Conditions</li>
    </ul>
  </div>

  <div class="footer-col" style="left:861px;width:240px">
    <h4>Contact Us</h4>
    <ul class="contact-list">
      <li><span class="ico"><svg width="14" height="16" viewBox="0 0 14 16"><path d="M7 1a5 5 0 0 0-5 5c0 4 5 9 5 9s5-5 5-9a5 5 0 0 0-5-5z" fill="#2a2320"/><circle cx="7" cy="6" r="2" fill="#fff"/></svg></span>Birchwell Hollow Cattle<br>United States</li>
      <li><span class="ico"><svg width="14" height="14" viewBox="0 0 14 14"><path d="M3 1l2 3-1.5 1.5a8 8 0 0 0 5 5L10 9l3 2-1 2C6 13 1 8 1 2z" fill="#2a2320"/></svg></span>250-555-0142</li>
      <li><span class="ico"><svg width="14" height="12" viewBox="0 0 14 12"><rect x="1" y="1" width="12" height="10" rx="1" fill="#2a2320"/><path d="M1 2l6 5 6-5" fill="none" stroke="#fff" stroke-width="1.3"/></svg></span>info@birchwellhollow.com</li>
    </ul>
  </div>

  <div class="footer-rule"></div>
  <p class="copyright">Copyrights@2026.Company Name.All Rights Reserved</p>
</footer>

</body>
</html>
```